Broschüre für Personaldienstleister
Zielgruppe
Wir sind ein Personaldienstleister und vermitteln ausländisches medizinisches Fachpersonal an deutsche Einrichtungen. Unsere Zielgruppe sind Krankenhäuser, Pflegeheime, Ärztehäuser, Praxen, Labore und weitere medizinische Institutionen.
Aufgabenstellung
Wir haben eine Infobroschüre sowie eine PowerPoint Präsentation bereits mit einem groben Design erstellt. Texte und Beispielbilder (Stockmaterial) sind ebenfalls vorhanden, gerne wünschen wir uns auch Eigeninitiative bei der Wahl der Bilder passend zum neuen Design.
Wir wünschen uns ein Redesign mit einem kreativen, einzigartigen Design. Zudem ist uns wichtig, dass unsere Infografiken qualitativ und hochwertig gestaltet werden.
Dieses Projekt ist mit zukünftigen Folgeprojekten verbunden, da wir weitere Präsentationen und Broschüren für andere Zielgruppen benötigen.

```html
<!DOCTYPE html>
<html lang="de">
<head>
<meta charset="utf-8">
<title>Veltaris HR – Broschüre</title>
<link href="https://fonts.googleapis.com/css2?family=Ubuntu:wght@400;500;700&family=Montserrat:wght@400;500;600;700;800&display=swap" rel="stylesheet">
<style>
:root{
  --bg:#e4e5e6;
  --paper:#f4f5f5;
  --ink:#1c4146;
  --teal-dark:#183f43;
  --green:#2f7c67;
  --green-mid:#3d8a73;
  --slate:#3a5c61;
  --band-dark:#1d4b48;
  --text:#4a5557;
  --map:#c9cccd;
  --photo-a:#b9c3c6;
  --photo-b:#3fb6cf;
  --pin-red:#d22a2a;
}
*{box-sizing:border-box;margin:0;padding:0}
html,body{width:1200px;height:872px;overflow:hidden;background:var(--bg)}
body{font-family:"Montserrat",sans-serif;color:var(--text);position:relative}
.spread{position:absolute;left:30px;top:46px;width:1140px;height:780px;display:flex;box-shadow:0 8px 30px rgba(0,0,0,.18)}
.page{position:relative;width:570px;height:780px;background:var(--paper);overflow:hidden}
.page--left{border-right:1px solid #d6d8d8}
.photo{position:absolute;left:0;top:0;width:570px;height:290px;background:linear-gradient(90deg,var(--photo-a) 0%,#d9dcdc 35%,#8e6d58 55%,var(--photo-b) 80%,#36a9c4 100%)}
.headline{position:absolute;left:34px;top:308px;font-family:"Ubuntu",sans-serif;font-weight:700;font-size:30px;color:var(--ink);white-space:nowrap}
.subline{position:absolute;left:34px;top:348px;font-family:"Ubuntu",sans-serif;font-weight:500;font-size:17px;color:var(--green)}
.col{position:absolute;top:380px;width:240px;font-size:10.5px;line-height:1.45}
.col--a{left:34px}
.col--b{left:298px}
.info{position:absolute;left:0;top:482px;width:570px;height:255px}
.tile{position:absolute;border-radius:18px;color:#fff;padding:14px 22px;font-size:7.5px;line-height:1.35}
.tile h3{font-size:9.5px;font-weight:600;margin-bottom:3px;line-height:1.2}
.tile--growth{left:70px;top:45px;width:200px;height:95px;background:var(--teal-dark);padding-left:44px;padding-right:30px}
.tile--cost{left:285px;top:25px;width:205px;height:90px;background:var(--green-mid);padding-left:60px}
.tile--sick{left:85px;top:150px;width:200px;height:100px;background:var(--green);padding-left:44px;padding-right:30px}
.tile--power{left:295px;top:135px;width:210px;height:100px;background:var(--slate);padding-left:52px;padding-right:30px}
.hub{position:absolute;left:228px;top:78px;width:110px;height:110px;border-radius:50%;background:var(--paper);border:3px solid #dfe3e2}
.hub::after{content:"";position:absolute;left:22px;top:22px;width:60px;height:60px;border-radius:50%;background:var(--green)}
.badge{position:absolute;width:52px;height:52px;border-radius:50%;border:5px solid var(--paper);display:flex;align-items:center;justify-content:center}
.badge svg{width:24px;height:24px}
.footer{position:absolute;left:0;bottom:0;width:570px;height:34px;background:var(--green);display:flex;align-items:center;justify-content:space-between;padding:0 30px;color:#fff;font-size:9.5px}
.footer::after{content:"";position:absolute;right:0;top:0;width:46px;height:34px;background:var(--band-dark)}
.footer span{position:relative;z-index:1}
.brand{position:absolute;left:0;width:570px;top:40px;text-align:center;font-family:"Ubuntu",sans-serif;font-weight:700;font-size:17px;color:var(--ink)}
.map-title{position:absolute;left:0;width:570px;top:70px;text-align:center;font-family:"Ubuntu",sans-serif;font-weight:400;font-size:17px;color:var(--ink)}
.map-title b{font-weight:700}
.map{position:absolute;left:40px;top:110px;width:490px;height:220px;background:radial-gradient(ellipse at center,var(--map) 0%,#dcdfe0 60%,var(--paper) 100%);border-radius:40px}
.total{position:absolute;left:0;width:570px;top:104px;text-align:center;font-family:"Ubuntu",sans-serif;font-weight:700;font-size:44px;color:var(--ink)}
.stat{position:absolute;font-size:8.5px;color:var(--ink);line-height:1.25}
.stat strong{display:block;font-family:"Ubuntu",sans-serif;font-size:24px;font-weight:700}
.stat--eu{left:40px;top:222px}
.stat--third{left:300px;top:200px}
.arrows{position:absolute;left:0;top:0;width:570px;height:360px}
.source{position:absolute;right:40px;top:316px;font-family:"Ubuntu",sans-serif;font-size:11px;color:var(--green)}
.body{position:absolute;left:40px;top:380px;width:490px;font-size:10.5px;line-height:1.5}
.body p{margin-bottom:14px}
</style>
</head>
<body>
<div class="spread">
  <section class="page page--left">
    <div class="photo" role="img" aria-label="Foto: erschöpfte Pflegekraft in türkiser Dienstkleidung im Klinikflur"></div>
    <h1 class="headline">Wenn die Fachkräfte fehlen...</h1>
    <h2 class="subline">Probleme &amp; Herausforderungen</h2>
    <p class="col col--a">Lorem ipsum dolor sit amet, graecequidam&shy;eoste, facetediceretvituperatoribusest at. Odioeratmnesarchumeiusu, neclabiturlob&shy;ortis at. Est albucius mandamus et. Ut pro option omnesque, accusatapartien&shy;dosedte. Euiusatquiignota maiorum. His</p>
    <p class="col col--b">nominaviexpetendainteresset an, te vitae abhor&shy;reanteum. Eiharumfierent vel. Eos eutheophras&shy;tusdefinitionem. Quo appeteretractatossententi&shy;ae id, ut duo hinctempor, omnesnominavisadip&shy;scingeumei. Necutnonumylaborelobortis, quod interessetpersequeris cu qui.</p>

    <div class="info">
      <div class="tile tile--growth"><h3>Wachstumshürden<br>&amp; Umsatzeinbußen</h3>Lorem ipsum dolor sit amet, graecequidameoste, facete&shy;diceretvituperatoribusest at.</div>
      <div class="tile tile--cost"><h3>Hohe<br>Aufwände</h3>Lorem ipsum dolor sit amet, graecequidameoste, facetedic&shy;eretvituperatoribusest at.</div>
      <div class="tile tile--sick"><h3>Hohe<br>Krankenquote</h3>Lorem ipsum dolor sit amet, graecequidameoste, facetedic&shy;eretvituperatoribusest at. Odioerat&shy;mnesarchumeiusu, neclabiturlobor&shy;tis at.</div>
      <div class="tile tile--power"><h3>Ungünstiges<br>Machtgefüge</h3>Lorem ipsum dolor sit amet, graecequidameoste, facetedic&shy;eretvituperatoribusest at. Odioeratmnesarchumeiusu, neclabiturlobortis at.</div>
      <div class="hub"></div>

      <div class="badge" style="left:50px;top:60px;background:var(--teal-dark)"><svg viewBox="0 0 24 24" fill="none" stroke="#fff" stroke-width="2"><path d="M3 20h18M6 18V8M10 18v-7M14 18v-4M18 18v-2M5 6l14 10"/></svg></div>
      <div class="badge" style="left:462px;top:0;background:var(--green-mid)"><svg viewBox="0 0 24 24" fill="none" stroke="#fff" stroke-width="2"><rect x="3" y="7" width="18" height="10" rx="1"/><circle cx="12" cy="12" r="2.5"/></svg></div>
      <div class="badge" style="left:60px;top:200px;background:var(--teal-dark)"><svg viewBox="0 0 24 24" fill="#fff"><rect x="4" y="14" width="3" height="6"/><rect x="9" y="11" width="3" height="9"/><rect x="14" y="8" width="3" height="12"/><path d="M14 4h6v6l-2-2-4 4-1-1 4-4z"/></svg></div>
      <div class="badge" style="left:485px;top:180px;background:var(--slate)"><svg viewBox="0 0 24 24" fill="none" stroke="#fff" stroke-width="1.6"><circle cx="12" cy="5" r="2"/><circle cx="5" cy="12" r="2"/><circle cx="19" cy="12" r="2"/><circle cx="8" cy="19" r="2"/><circle cx="16" cy="19" r="2"/><path d="M12 7v4M7 12h10M12 11l-4 6M12 11l4 6"/></svg></div>
    </div>

    <footer class="footer"><span>+49 211 580 37 190</span><span>team@veltaris-hr.de</span><span style="margin-right:50px">www.veltaris-hr.de</span></footer>
  </section>

  <section class="page page--right">
    <div class="brand">Veltaris HR</div>
    <div class="map" role="img" aria-label="Gepunktete Weltkarte als Hintergrund der Infografik"></div>
    <h2 class="map-title">Jährlilcher <b>Zuwanderungsbedarf</b> Deutschlands</h2>
    <div class="total">260.000</div>

    <svg class="arrows" viewBox="0 0 570 360" aria-hidden="true">
      <path d="M165 290 Q200 310 224 268" fill="none" stroke="var(--green)" stroke-width="12" stroke-linecap="round"/>
      <path d="M210 264 L232 244 L238 274 Z" fill="var(--green)"/>
      <path d="M330 175 Q290 155 255 180" fill="none" stroke="var(--green)" stroke-width="12" stroke-linecap="round"/>
      <path d="M240 185 L262 166 L266 192 Z" fill="var(--green)"/>
      <path d="M208 185 a20 20 0 1 1 40 0 c0 14 -20 34 -20 34 s-20 -20 -20 -34z" fill="var(--ink)"/>
      <circle cx="228" cy="185" r="9" fill="var(--paper)"/>
      <path d="M460 175 a18 18 0 1 1 36 0 c0 12 -18 30 -18 30 s-18 -18 -18 -30z" fill="var(--pin-red)"/>
      <circle cx="478" cy="175" r="8" fill="var(--paper)"/>
    </svg>

    <div class="stat stat--eu"><strong>114.000</strong>Zuwanderer aus anderen<br><b>EU-Staaten</b> erwartet</div>
    <div class="stat stat--third"><strong>146.000</strong><b>Zuwanderer aus Drittstaaten<br>außerhalb der Eu benötigt</b></div>
    <div class="source">Quelle: Korvenstiftung</div>

    <div class="body">
      <p>Lorem ipsum dolor sit amet, consectetur adipiscing elit. Quisque accumsan bibendum rutrum. Curabitur non nunc laoreet, faucibus lectus non, elementum justo. Curabitur nec massa sit amet lectus tempus interdum a sit amet nisi. Maecenas ultrices diam vel malesuada condimentum. Donec efficitur, justo in mattis semper, sem purus congue orci, imperdiet suscipit dui sapien nec tellus. Morbi auctor, elit eu laoreet consequat, tortor dui volutpat metus, eu congue mi arcu et nulla. Cras semper fringilla nisi ut eleifend. Quisque nisl tortor, molestie non enim eu, hendrerit imperdiet nunc.</p>
      <p>Pellentesque habitant morbi tristique senectus et netus et malesuada fames ac turpis egestas. Integer justo eros, vehicula id magna nec, dapibus lobortis ante. Nam ac ligula est. Aliquam rhoncus laoreet mi, at pulvinar mauris lobortis sed. Phasellus fringilla ipsum eros, a vulputate mi vehicula id. Donec vitae hendrerit libero, in elementum metus. Ut tristique neque nisi, et feugiat nibh molestie at. Aliquam sit amet erat eleifend, viverra nibh varius, aliquet felis.</p>
      <p>Suspendisse sodales justo ac diam tincidunt, vehicula finibus velit maximus. Nunc ut faucibus quam. Nulla facilisis tempor leo nec eleifend. Aliquam vitae auctor lorem. Cras placerat eget nisl sed vulputate. Nulla viverra iaculis ipsum. Sed elit mauris, vehicula id arcu vitae, cursus posuere urna. Suspendisse potenti.</p>
    </div>

    <footer class="footer"><span>+49 211 580 37 190</span><span>team@veltaris-hr.de</span><span style="margin-right:50px">www.veltaris-hr.de</span></footer>
  </section>
</div>
</body>
</html>
```